Oil Field Service company needs professional business cards

Looking to clean up our current company business cards and look a little more professional. Brenwick Casing Services is a US based company that services the oil field. We deal with engineers, managers and oil rigs....................................................................................................................................................................................................................................................................................................................................................................................................

Target Market(s)

Oil and Gas professionals

Industry/Entity Type

Oil And Gas

Contact Information for Business Card

See attached photo as example

Font styles to use
Sans Serif

Colors
ec1f27

Requirements
Must have
• Company Logo, Name, Title, Cell, Office, Fax, Email.
• See attached photo
Nice to have
• External CRT, Internal CRT, Casing Crews, Torque Turn, Laydown Machine
Should not have
• Do not introduce any new pictures and keep it professional looking

```html
<!DOCTYPE html>
<html lang="en">
<head>
<meta charset="utf-8">
<title>Brenwick Casing Services – Business Card</title>
<link href="https://fonts.googleapis.com/css2?family=Roboto+Condensed:wght@400;700&family=Montserrat:wght@600;700&display=swap" rel="stylesheet">
<style>
  :root {
    --slate: #48535f;
    --slate-dark: #3d4752;
    --red: #ec1f27;
    --paper: #f7f7f6;
    --ink: #3a4450;
    --backdrop: #e4e4e4;
    --white: #ffffff;
  }
  * { margin: 0; padding: 0; box-sizing: border-box; }
  html, body { width: 1200px; height: 873px; overflow: hidden; }
  body {
    background: var(--backdrop);
    font-family: "Roboto Condensed", Arial, sans-serif;
    position: relative;
  }
  .card {
    position: absolute;
    top: 282px;
    width: 540px;
    height: 309px;
    box-shadow: 0 6px 14px rgba(0,0,0,.18);
    overflow: hidden;
  }
  /* Front */
  .card-front { left: 40px; background: var(--slate); }
  .front-brand {
    position: absolute; left: 0; right: 0; top: 104px;
    text-align: center; color: var(--white);
    font-family: "Montserrat", Arial, sans-serif; font-weight: 700;
  }
  .front-brand .brand-name { font-size: 44px; letter-spacing: 1px; line-height: 1; }
  .front-brand .brand-sub { font-size: 15px; letter-spacing: 4px; margin-top: 14px; }
  .service-band {
    position: absolute; left: 0; right: 0; top: 268px; height: 19px;
    background: var(--red); color: var(--white);
    font-size: 12.5px; line-height: 19px; text-align: center;
    word-spacing: 1px;
  }
  .service-band .sep { margin: 0 6px; }

  /* Back */
  .card-back { left: 620px; background: var(--paper); }
  .back-brand {
    position: absolute; left: 50px; width: 214px; top: 126px;
    text-align: center; color: var(--ink);
    font-family: "Montserrat", Arial, sans-serif; font-weight: 700;
  }
  .back-brand .brand-name { font-size: 29px; line-height: 1; letter-spacing: .5px; }
  .back-brand .brand-sub { font-size: 10px; letter-spacing: 2.2px; margin-top: 9px; }
  .divider {
    position: absolute; left: 272px; top: 102px; width: 2px; height: 94px;
    background: var(--red);
  }
  .contact { position: absolute; left: 300px; top: 104px; color: var(--ink); }
  .contact .person { font-size: 19px; font-weight: 700; line-height: 1.1; }
  .contact .role { font-size: 13px; color: var(--red); margin-top: 2px; }
  .contact .cell { font-size: 13px; margin-top: 18px; }
  .contact .cell b { color: var(--red); font-weight: 400; }
  .contact .email { font-size: 13px; margin-top: 2px; }
  .office-band {
    position: absolute; left: 0; right: 0; bottom: 0; height: 53px;
    background: var(--slate); border-top: 4px solid var(--red);
    color: var(--white); text-align: center; font-size: 12.5px; line-height: 15px;
    padding-top: 9px;
  }
  .office-band .sep { margin: 0 6px; }
</style>
</head>
<body>
  <section class="card card-front" aria-label="Card front">
    <div class="front-brand">
      <div class="brand-name">BRENWICK</div>
      <div class="brand-sub">CASING SERVICES</div>
    </div>
    <div class="service-band">External CRT<span class="sep">|</span>Internal CRT<span class="sep">|</span>Casing Crews<span class="sep">|</span>Torque Turn<span class="sep">|</span>Laydown Machine</div>
  </section>

  <section class="card card-back" aria-label="Card back">
    <div class="back-brand">
      <div class="brand-name">BRENWICK</div>
      <div class="brand-sub">CASING SERVICES</div>
    </div>
    <div class="divider"></div>
    <div class="contact">
      <div class="person">Cody Harlan</div>
      <div class="role">Area Manager</div>
      <div class="cell"><b>C.</b> (555) 017-3381</div>
      <div class="email">charlan@brenwickcs.com</div>
    </div>
    <div class="office-band">
      <div>Redmesa, OK 73850</div>
      <div>P. (555) 014-2700<span class="sep">|</span>F. (555) 014-2730<span class="sep">|</span>www.brenwickcs.com</div>
    </div>
  </section>
</body>
</html>
```